High-end law practice specializing in closely held business succession planning and complex estates

Solo practitioner whose practice specializes in high-net worth, complex estate planning needs muliple versions of letterhead black and white, please. Letterhead should incorporate slogan, "Protecting your family business is my business," for one and "Complex Estate Planning"; third with no slogan. All for The Law Office of Marcy Lynn Pettibone, PC, 418 Cedar Hollow Ln., Newport News, Virginia 23648, Tel. 757-555-0142 Fax tbd email: marcy@mlplawgroup.example; Marcy Lynn Pettibone, Esq., principal, licensed in VA, NY, DC
Updates

Project Deadline Extended
Reason: My internet service went down and I can only view designs on my smart phone -- it's just too hard to review. So sorry! Working with my ISP now. Please be patient!

Target Market(s)

High net worth clients with complex estate planning needs, family businesses, family farmers, family foresters -- people with unique estate/succession planning needs who need a specialist who understands them.

Industry/Entity Type

Business

Font styles to use
Script

Requirements
Must have
• A high-end look and feel, connoting trustworthiness, special knowledge, and expertise.

```html
<!DOCTYPE html>
<html lang="en">
<head>
<meta charset="utf-8">
<title>The Law Office of Marcy Lynn Pettibone, PC – Letterhead</title>
<link rel="stylesheet" href="https://fonts.googleapis.com/css2?family=Source+Sans+3:wght@400;700&display=swap">
<style>
  :root {
    --backdrop: #e6e4e1;
    --paper: #ffffff;
    --ink: #111111;
    --rule: #bdbdbd;
    --band: #000000;
  }
  html, body {
    margin: 0;
    padding: 0;
    width: 953px;
    height: 1200px;
    overflow: hidden;
    background: var(--backdrop);
  }
  .canvas {
    position: relative;
    width: 953px;
    height: 1200px;
    font-family: "Source Sans 3", "Myriad Pro", Arial, sans-serif;
    color: var(--ink);
  }
  .letterhead {
    position: absolute;
    left: 139px;
    top: 153px;
    width: 676px;
    height: 950px;
    background: var(--paper);
    box-shadow: 0 2px 6px rgba(0,0,0,0.12);
  }
  .firm {
    position: absolute;
    left: 32px;
    top: 32px;
  }
  .firm-name {
    margin: 0;
    font-weight: 700;
    font-size: 19.5px;
    line-height: 23px;
    letter-spacing: 0.1px;
    text-transform: uppercase;
  }
  .firm-credentials {
    margin: 3px 0 0;
    font-size: 12.5px;
    line-height: 16px;
  }
  .contact {
    position: absolute;
    left: 469px;
    top: 34px;
    padding-left: 7px;
    border-left: 1px solid var(--rule);
    font-size: 11px;
    line-height: 15.5px;
  }
  .contact p { margin: 0; }
  .contact .address { margin-bottom: 3px; }
  .slogan {
    position: absolute;
    left: 0;
    right: 0;
    top: 913px;
    margin: 0;
    text-align: center;
    font-size: 15px;
    line-height: 18px;
  }
  .base-band {
    position: absolute;
    left: 0;
    right: 0;
    bottom: -5px;
    height: 10px;
    background: var(--band);
  }
</style>
</head>
<body>
<main class="canvas">
  <section class="letterhead">
    <header class="firm">
      <h1 class="firm-name">The Law Office<br>of Marcy Lynn Pettibone, PC</h1>
      <p class="firm-credentials">Marcy Lynn Pettibone, Esq., licensed in VA, NY, DC</p>
    </header>
    <address class="contact" style="font-style: normal;">
      <div class="address">
        <p>418 Cedar Hollow Ln.,</p>
        <p>Newport News, Virginia 23648</p>
      </div>
      <p>T: 757-555-0142 | F: 757-555-0199</p>
      <p>E: marcy@mlplawgroup.example</p>
    </address>
    <p class="slogan">Complex Estate Planning</p>
    <div class="base-band"></div>
  </section>
</main>
</body>
</html>
```